Im want a website LIKE VRX's and FleetHollow.com's with product payment options like Trenzo's

I need a website LIKE VRX with a header made EXACTLY LIKE THAT OF FLEETHOLLOWS .

The front page photo should be like that of FLEETHOLLOW's webpage as well.

The name of the website will be called "M.K. (Caldera Key)".

We will be targeting ALL MARKETS in a small town in central Panama and charging businesses "listing fees" like a phone book does but also providing informational blogs, news, and other interesting activities.

THIS IS A MULTI PAGE WEBSITE

THIS IS WHERE VRX's website meets Brivelle/FleetHollow.

Once the layout is built I will tweak and modify, add information, and upload items for sale.

Here is a list of specific categories that should be listed out above the front page header image/search bar

-- Home -- News -- Travel -- Activities -- Shop & Dine -- Store -- More... --

These categories should be spread across the bottom of the page in three sections:

WHATS SO GREAT ABOUT (Caldera Key),
HAND PICKED TOURS
ACTIVITIES etc.

Also lets use www.Trenzo.example 's
"HOT DESTINATIONS"
"BEAT THE BEST PRICES IN BOQUETE"
"OCTOBERS INSIDER PICKS"
"TOP DESTINATIONS"
and spread them in four sections side-by-side near the bottom of the page.

Overall I would like to see the finished product to be something LIKE VRX's and FleetHollows.

WE NEED ONLINE PAYMENT OPTIONS LIKE BRIVELLE'S WEBSITE HAS

This will be a desktop website but should be very mobile friendly as well.

-rodmund

P.S. Good luck!

If it isn't already too late to change the website name, the name of the website should be "Caldera Key". Added Friday, October 9, 2015

What do you guys think the budget should be to win this? Added Saturday, October 10, 2015

www.palmorra.example is the most amazing simple site. Whoever can make me a replica with my specifications will win immediately!!!! Added Sunday, October 18, 2015

OMG www.palmorra.example is the bomb!So simple and elegant. Whoever can make me an EXACT REPLICA OF WWW.PALMORRA.EXAMPLE as my site with the specifications mentioned in my brief will take home the $825.00 immediately! Good luck amigos! Added Sunday, October 18, 2015

Does anybody know how to add recurring monthly billing options on this website? Added Sunday, October 18, 2015

ALL MARKETS

Product

Coded - Design and coding required

5+ page

• Coinvey payment options.
• I must be able to add and remove photos/text and video from the HTML files in the page.
• Be creative my friends, and may the odds be forever in your favor!
• I added some photos of a good layout for our page below.

```html
<!DOCTYPE html>
<html lang="en">
<head>
<meta charset="utf-8">
<title>Caldera Key — Paris and Bordeaux</title>
<link href="https://fonts.googleapis.com/css2?family=Roboto:wght@300;400;500;700&family=Open+Sans:ital,wght@0,400;0,600;0,700;1,400&display=swap" rel="stylesheet">
<style>
:root{
  --teal:#23a6b8;
  --teal-dark:#1a8a9a;
  --ink:#2d3439;
  --text:#666d72;
  --muted:#9aa1a6;
  --line:#e3e6e8;
  --head-bg:#1a262d;
  --top-bg:#131d22;
  --foot-bg:#2a2f33;
  --foot-bottom:#1f2326;
  --soft:#f4f6f7;
  --blue-card:#3a84c9;
  --red-card:#d9473b;
  --white:#ffffff;
}
*{box-sizing:border-box;margin:0;padding:0}
html,body{width:1200px;height:2508px;overflow:hidden}
body{font-family:"Open Sans",Arial,sans-serif;font-size:12px;color:var(--text);background:var(--white);line-height:1.6}
h1,h2,h3,h4,.nav a,.btn{font-family:"Roboto",Arial,sans-serif}
.wrap{width:910px;margin:0 auto;position:relative}

/* header */
.topbar{height:36px;background:var(--top-bg)}
.topbar .wrap{display:flex;justify-content:space-between;align-items:center;height:36px}
.social-dots{display:flex;gap:6px}
.social-dots span{width:18px;height:18px;border-radius:50%;background:var(--teal)}
.contact{display:flex;gap:22px;color:#c9d3d7;font-size:11px}
.contact span{display:flex;align-items:center;gap:6px}
.navbar{height:64px;background:var(--head-bg)}
.navbar .wrap{display:flex;justify-content:space-between;align-items:center;height:64px}
.brand{display:flex;align-items:center;gap:8px;color:var(--white);font-family:"Roboto",sans-serif;font-size:24px;font-weight:400}
.brand i{width:12px;height:12px;background:var(--teal);display:block}
.nav{display:flex;height:64px}
.nav a{color:#e4ecef;text-decoration:none;font-size:11px;font-weight:500;padding:0 14px;display:flex;align-items:center;letter-spacing:.5px}
.nav a.active{background:var(--teal)}

.hero{height:160px;background:linear-gradient(90deg,#1d97a9 0%,#2bb0c0 55%,#1f8fa0 100%)}
.hero .wrap{padding-top:36px}
.hero h1{color:var(--white);font-size:34px;font-weight:400;line-height:1.2}
.hero p{color:#dff3f6;font-size:13px;margin-top:4px}

/* main */
.main{display:flex;gap:60px;padding-top:12px;height:1580px}
.content{width:650px}
.sidebar{width:200px}

.tour-top{display:flex;gap:24px;align-items:flex-end}
.photo{display:block;background:linear-gradient(180deg,#f1c99a 0%,#b7a392 55%,#5e6b5a 100%)}
.tour-photo{width:430px;height:240px}
.facts{margin-top:16px;width:430px;display:flex;justify-content:space-between;align-items:center}
.facts ul{list-style:none;font-size:11px}
.facts li{display:flex;gap:6px;align-items:center;line-height:22px}
.facts b{color:var(--ink);font-weight:600}
.dot{width:8px;height:8px;border-radius:50%;background:var(--teal);display:inline-block}
.btn{background:var(--teal);color:var(--white);font-size:12px;font-weight:500;padding:9px 18px;border-radius:2px}

.quote{margin:36px 0 0 40px;padding-left:16px;border-left:3px solid var(--teal);font-style:italic;font-size:14px;color:var(--muted);line-height:1.65;width:520px}

.map{margin-top:64px;height:268px;width:650px;background:linear-gradient(135deg,#e8ebe4 0%,#dde4e8 50%,#eceae2 100%);border:1px solid var(--line)}

.schedule{margin-top:30px;width:650px;border-collapse:collapse;font-size:10px}
.schedule th{background:var(--soft);color:var(--ink);font-weight:600;text-transform:uppercase;font-size:9px;letter-spacing:.5px}
.schedule th,.schedule td{border:1px solid var(--line);height:36px;text-align:center}

.para{margin-top:14px;font-size:11px;line-height:1.7}
.para b{color:var(--ink)}

.feature{margin-top:16px;display:flex;gap:24px}
.feature-photo{width:270px;height:190px;background:linear-gradient(180deg,#2f4a6e 0%,#6f6e8a 50%,#d68b56 100%)}
.feature h3{font-size:17px;font-weight:400;color:var(--ink);margin:14px 0 10px}
.ticks{list-style:none;font-size:11px}
.ticks li{display:flex;gap:8px;align-items:center;line-height:24px}

.tabs{margin-top:22px;display:flex;gap:22px;border-bottom:1px solid var(--line)}
.tabs span{font-family:"Roboto",sans-serif;font-size:13px;color:var(--ink);padding-bottom:6px}
.tabs span.on{color:var(--teal);border-bottom:2px solid var(--teal)}
.tab-body{margin-top:10px;font-size:11px;line-height:1.7}
.tab-body b{color:var(--ink)}

.share{margin-top:30px}
.share h4{font-size:12px;color:var(--ink);font-weight:500;margin-bottom:8px}
.share div{display:flex;gap:8px}
.share span{width:22px;height:22px;border-radius:50%;background:#4a5a66}

/* sidebar */
.side-title{font-size:13px;font-weight:500;color:var(--ink);text-transform:uppercase;letter-spacing:.4px;padding-bottom:8px;border-bottom:1px solid var(--line);margin-bottom:12px}
.dest{display:flex;gap:10px;margin-bottom:14px}
.dest .photo{width:56px;height:50px;flex:none}
.dest h4{font-size:12px;font-weight:500;color:var(--teal);line-height:1.3}
.dest p{font-size:9px;color:var(--muted);line-height:1.5}
.dest .price{color:var(--red-card);font-weight:600}
.comments{list-style:none;margin-bottom:30px}
.comments li{font-size:10px;line-height:1.5;padding:5px 0;border-bottom:1px dotted var(--line);display:flex;gap:6px;align-items:flex-start}
.comments li em{font-style:normal;color:var(--teal)}
.comments .dot{margin-top:5px;flex:none;width:6px;height:6px}
.tags{display:flex;flex-wrap:wrap;gap:5px}
.tags span{background:var(--teal);color:var(--white);font-size:9px;padding:3px 8px;border-radius:2px}

/* tweet band */
.tweet{height:148px;background:var(--teal)}
.tweet .wrap{display:flex;align-items:center;gap:30px;height:148px}
.tweet .bird{width:38px;height:38px;border-radius:50%;background:var(--white);flex:none;opacity:.9}
.tweet p{color:var(--white);font-size:11px;line-height:1.6;flex:1}
.tweet .arrows{display:flex;gap:4px}
.tweet .arrows span{width:20px;height:20px;background:rgba(255,255,255,.25);display:flex;align-items:center;justify-content:center}

/* footer */
.footer{height:472px;background:var(--foot-bg);color:#a8b0b5}
.footer .wrap{display:flex;gap:50px;padding-top:36px}
.f-about{width:270px;font-size:10px;line-height:1.7}
.f-about .brand{font-size:22px;margin-bottom:14px}
.badges{display:flex;gap:10px;margin-top:22px}
.badges span{width:54px;height:28px;border-radius:14px;background:#464d52}
.f-deals{width:250px}
.f-deals h3{color:var(--white);font-size:14px;font-weight:500;text-transform:uppercase;margin-bottom:16px;letter-spacing:.4px}
.deal{display:flex;gap:10px;margin-bottom:14px}
.deal .photo{width:54px;height:44px;flex:none}
.deal h4{color:var(--white);font-size:12px;font-weight:400;line-height:1.3}
.deal p{font-size:9px}
.f-promos{width:290px;display:flex;flex-direction:column;gap:18px;padding-top:6px}
.promo{height:120px;color:var(--white);display:flex;align-items:center;justify-content:flex-end;padding-right:26px;text-align:center;position:relative}
.promo.blue{background:linear-gradient(135deg,#2f6fb0,#4a9ad8)}
.promo.red{background:linear-gradient(135deg,#b8362d,#e55a47)}
.promo strong{display:block;font-family:"Roboto",sans-serif;font-size:26px;font-weight:300;line-height:1.1}
.promo small{font-size:11px}
.promo .pbtn{display:inline-block;margin-top:6px;border:1px solid rgba(255,255,255,.8);font-size:10px;padding:2px 10px}
.footbar{height:48px;background:var(--foot-bottom);color:#7b8388;font-size:10px;display:flex;align-items:center;justify-content:center}
</style>
</head>
<body>

<header>
  <div class="topbar">
    <div class="wrap">
      <div class="social-dots"><span></span><span></span><span></span><span></span><span></span><span></span></div>
      <div class="contact">
        <span><svg width="11" height="9" viewBox="0 0 11 9"><rect x=".5" y=".5" width="10" height="8" fill="none" stroke="#23a6b8"/><path d="M.5 .5l5 4 5-4" fill="none" stroke="#23a6b8"/></svg>info@calderakey.example</span>
        <span><svg width="10" height="10" viewBox="0 0 10 10"><path d="M2 1l2 2-1 1.5c.8 1.5 1.5 2.2 3 3L7.5 6.5l2 2L8 10C4 9.5.5 6 0 2z" fill="#23a6b8"/></svg>+1 555 0142 880</span>
      </div>
    </div>
  </div>
  <div class="navbar">
    <div class="wrap">
      <div class="brand"><i></i>Caldera Key</div>
      <nav class="nav">
        <a href="#">HOME</a><a href="#">PAGES</a><a href="#" class="active">PACKAGE</a><a href="#">LOCATIONS</a><a href="#">BLOG</a><a href="#">SHORTCODES</a><a href="#">CONTACT US</a>
      </nav>
    </div>
  </div>
  <section class="hero">
    <div class="wrap">
      <h1>Paris and Bordeaux</h1>
      <p>Sollicitudin Adipiscing Purus</p>
    </div>
  </section>
</header>

<div class="wrap main">
  <main class="content">
    <div class="photo tour-photo" role="img" aria-label="Photo of the Eiffel Tower at sunset over Paris"></div>
    <div class="facts">
      <ul>
        <li><span class="dot"></span><b>Duration:</b> 01 Nov 2015 – 08 Nov 2015</li>
        <li><span class="dot"></span><b>Location:</b> France</li>
        <li><span class="dot"></span><b>Available Seats:</b> 10</li>
        <li><span class="dot"></span><b>Price:</b> $1,250</li>
      </ul>
      <span class="btn">Book Now</span>
    </div>

    <blockquote class="quote">Donec ullamcorper nulla non metus auctor fringilla. Vestibulum id ligula porta felis euismod semper. Pellentesque ornare sem lacinia quam venenatis vestibulum.</blockquote>

    <div class="map" role="img" aria-label="Street map showing the tour meeting point"></div>

    <table class="schedule">
      <tr><th>Ticket From</th><th>Destination</th><th>Date</th><th>Departs</th><th>Arrives</th></tr>
      <tr><td>Seattle</td><td>Paris</td><td>Nov 01</td><td>08:30</td><td>18:45</td></tr>
      <tr><td>Paris</td><td>Bordeaux</td><td>Nov 04</td><td>10:15</td><td>13:20</td></tr>
      <tr><td>Bordeaux</td><td>Seattle</td><td>Nov 08</td><td>11:00</td><td>21:40</td></tr>
    </table>

    <p class="para"><b>Morbi leo risus, porta ac consectetur ac, vestibulum at eros.</b> Donec ullamcorper nulla non metus auctor fringilla. Maecenas sed diam eget risus varius blandit sit amet non magna. Curabitur blandit tempus porttitor. Lorem ipsum dolor sit amet, consectetur adipiscing elit. Aenean lacinia bibendum nulla sed consectetur. Nullam quis risus eget urna mollis ornare vel eu leo. Vivamus sagittis lacus vel augue laoreet rutrum faucibus dolor auctor. Cras mattis consectetur purus sit amet fermentum.</p>

    <div class="feature">
      <div class="feature-photo" role="img" aria-label="Evening view of a Paris street along the river"></div>
      <div>
        <h3>Mollis Ipsum Mattis Commodo</h3>
        <ul class="ticks">
          <li><svg width="10" height="10" viewBox="0 0 10 10"><path d="M1 5l3 3 5-6" fill="none" stroke="#23a6b8" stroke-width="2"/></svg>Aenean lacinia bibendum nulla sed</li>
          <li><svg width="10" height="10" viewBox="0 0 10 10"><path d="M1 5l3 3 5-6" fill="none" stroke="#23a6b8" stroke-width="2"/></svg>Cum sociis natoque penatibus et magnis</li>
          <li><svg width="10" height="10" viewBox="0 0 10 10"><path d="M1 5l3 3 5-6" fill="none" stroke="#23a6b8" stroke-width="2"/></svg>Vestibulum id ligula porta felis</li>
          <li><svg width="10" height="10" viewBox="0 0 10 10"><path d="M1 5l3 3 5-6" fill="none" stroke="#23a6b8" stroke-width="2"/></svg>Nullam quis risus eget urna mollis</li>
          <li><svg width="10" height="10" viewBox="0 0 10 10"><path d="M1 5l3 3 5-6" fill="none" stroke="#23a6b8" stroke-width="2"/></svg>Cras justo odio, dapibus ac facilisis</li>
        </ul>
      </div>
    </div>

    <div class="tabs"><span class="on">Day1</span><span>Day2</span><span>Day3</span><span>Day4</span></div>
    <p class="tab-body"><b>Aenean eu leo quam pellentesque ornare.</b> Sem lacinia quam venenatis vestibulum. Donec ullamcorper nulla non metus auctor fringilla. Integer posuere erat a ante venenatis dapibus posuere velit aliquet. Maecenas faucibus mollis interdum, fusce dapibus tellus ac cursus commodo.</p>

    <div class="share">
      <h4>Social Share</h4>
      <div><span></span><span></span><span></span><span></span><span></span><span></span><span></span><span></span></div>
    </div>
  </main>

  <aside class="sidebar">
    <h3 class="side-title">Hot Destinations</h3>
    <div class="dest"><div class="photo" role="img" aria-label="City skyline at dusk"></div><div><h4>Rome, Milan, Madrid</h4><p>6 days · 20% off · <span class="price">$1,250</span></p></div></div>
    <div class="dest"><div class="photo" role="img" aria-label="Historic ruins in Rome"></div><div><h4>Rome City Tour</h4><p>4 days · 20% off · <span class="price">$890</span></p></div></div>
    <div class="dest"><div class="photo" role="img" aria-label="Bay bridge in San Francisco"></div><div><h4>San Francisco</h4><p>5 days · 20% off · <span class="price">$1,040</span></p></div></div>
    <div class="dest"><div class="photo" role="img" aria-label="Open savanna landscape"></div><div><h4>Wild Life Tour</h4><p>7 days · 20% off · <span class="price">$1,460</span></p></div></div>

    <h3 class="side-title" style="margin-top:20px">Recent Comments</h3>
    <ul class="comments">
      <li><span class="dot"></span><span>travel guest on <em>Post With Video Thumbnail</em></span></li>
      <li><span class="dot"></span><span>travel guest on <em>Post With Video Thumbnail</em></span></li>
      <li><span class="dot"></span><span>travel guest on <em>Post With Video Thumbnail</em></span></li>
      <li><span class="dot"></span><span>editor on <em>Post With Left Sidebar</em></span></li>
      <li><span class="dot"></span><span>admin on <em>This is a Single Sliver Post</em></span></li>
    </ul>

    <h3 class="side-title">Tags</h3>
    <div class="tags"><span>agency</span><span>blog</span><span>business</span><span>ceremony</span><span>corporate</span><span>conference</span><span>design</span><span>events</span><span>party</span><span>portfolio</span><span>travel</span><span>wedding</span></div>
  </aside>
</div>

<section class="tweet">
  <div class="wrap">
    <span class="bird"></span>
    <p>RT @CalderaKeyTrips: "Waking up in the right place is probably more important than working hard" — Lessons from Road Journeys<br>2 days ago</p>
    <div class="arrows">
      <span><svg width="8" height="8" viewBox="0 0 8 8"><path d="M6 0L2 4l4 4" fill="none" stroke="#fff" stroke-width="1.5"/></svg></span>
      <span><svg width="8" height="8" viewBox="0 0 8 8"><path d="M2 0l4 4-4 4" fill="none" stroke="#fff" stroke-width="1.5"/></svg></span>
    </div>
  </div>
</section>

<footer class="footer">
  <div class="wrap">
    <div class="f-about">
      <div class="brand"><i></i>Caldera Key</div>
      <p>Pellentesque habitant morbi tristique senectus et netus et malesuada fames ac turpis egestas. Donec ullamcorper nulla non metus auctor fringilla. Nullam quis risus eget urna mollis ornare vel eu leo. Cum sociis natoque penatibus et magnis dis parturient montes nascetur ridiculus mus.</p>
      <div class="badges"><span></span><span></span><span></span><span></span></div>
    </div>
    <div class="f-deals">
      <h3>Last Minute Deals</h3>
      <div class="deal"><div class="photo" role="img" aria-label="City skyline"></div><div><h4>Rome, Milan, Madrid</h4><p>20% off · $1,250</p></div></div>
      <div class="deal"><div class="photo" role="img" aria-label="Historic ruins"></div><div><h4>Rome City Tour</h4><p>20% off · $890</p></div></div>
      <div class="deal"><div class="photo" role="img" aria-label="Bay bridge"></div><div><h4>San Francisco</h4><p>20% off · $1,040</p></div></div>
      <div class="deal"><div class="photo" role="img" aria-label="Savanna landscape"></div><div><h4>Wild Life Tour</h4><p>20% off · $1,460</p></div></div>
    </div>
    <div class="f-promos">
      <div class="promo blue"><div><strong>20% Off</strong><small>Rome City Tour</small><br><span class="pbtn">Book Now</span></div></div>
      <div class="promo red"><div><strong>20% Off</strong><small>San Francisco</small><br><span class="pbtn">Book Now</span></div></div>
    </div>
  </div>
</footer>
<div class="footbar">Copyright © 2015 All Right Reserved by Caldera Key</div>

</body>
</html>
```